Redesign business cards

We have a new logo and I am not that happy with the layout of our existing card and looking for a change. Font is a bit small and the green can be hard to read. Logo may need a tidy up as the copy I have is not that hi-res too so require you to produce a hi-res version of the logo for us too. There will be three individual business cards to produce with just the names and phone numbers being different. Address will change too, but use what you see on the card for now.

Industry/Entity Type

Business

Requirements
Nice to have
• You could consider a redesign to the new logo, just not too radical. We like the blue and green hexagons as we feel that they are representative of oil industry that we are in.

```html
<!DOCTYPE html>
<html lang="en">
<head>
<meta charset="utf-8">
<title>Terralin Oil Services – Business Cards</title>
<link href="https://fonts.googleapis.com/css2?family=Open+Sans:wght@400;600;700&display=swap" rel="stylesheet">
<style>
  :root {
    --bg: #e9e7e3;
    --card: #ffffff;
    --blue: #1fa9e6;
    --green: #7cc142;
    --orange: #f28c1c;
    --grey: #7d7f82;
    --ink: #3b3d40;
    --on-blue: #ffffff;
  }
  * { margin: 0; padding: 0; box-sizing: border-box; }
  html, body { width: 1200px; height: 829px; overflow: hidden; }
  body {
    background: var(--bg);
    font-family: "Open Sans", Arial, sans-serif;
    position: relative;
  }
  .card {
    position: absolute;
    top: 264px;
    width: 520px;
    height: 300px;
    background: var(--card);
    box-shadow: 0 6px 18px rgba(0,0,0,.14);
    overflow: hidden;
  }
  .card--front { left: 50px; }
  .card--back { left: 630px; }

  .front__band { position: absolute; inset: 0; }

  .brand { position: absolute; }
  .brand__name {
    display: flex; align-items: center; gap: 8px;
    color: var(--blue);
    font-weight: 700;
    line-height: 1;
  }
  .brand__dot { border-radius: 50%; background: var(--green); flex: none; }
  .brand__tag { color: var(--grey); font-weight: 400; line-height: 1; }

  .card--front .brand { left: 34px; top: 40px; }
  .card--front .brand__name { font-size: 38px; }
  .card--front .brand__dot { width: 14px; height: 14px; }
  .card--front .brand__tag { font-size: 16px; margin: 4px 0 0 2px; }

  .person {
    position: absolute; left: 36px; top: 118px;
    font-size: 15px; color: var(--orange); font-weight: 700;
  }
  .person__role { color: var(--grey); font-weight: 400; font-size: 11px; }

  .contact {
    position: absolute; left: 200px; right: 20px; top: 160px;
    color: var(--on-blue); font-size: 11.5px; line-height: 1.75;
    text-align: center;
  }
  .contact__row { display: flex; justify-content: center; align-items: center; gap: 6px; }
  .contact__icon { width: 11px; height: 11px; flex: none; }
  .contact__gap { width: 10px; }

  .card--back .brand {
    left: 0; right: 0; top: 100px;
    display: flex; flex-direction: column; align-items: center;
  }
  .card--back .brand__name { font-size: 50px; }
  .card--back .brand__dot { width: 18px; height: 18px; }
  .card--back .brand__tag { font-size: 20px; margin-top: 6px; }
  .back__web {
    position: absolute; left: 0; right: 0; top: 214px;
    text-align: center; color: var(--ink);
    font-size: 13px; letter-spacing: 3px; font-weight: 600;
  }
</style>
</head>
<body>
  <section class="card card--front">
    <svg class="front__band" viewBox="0 0 520 300" width="520" height="300" aria-hidden="true">
      <polygon points="0,300 250,168 520,100 520,300" fill="var(--blue)"/>
    </svg>

    <div class="brand">
      <div class="brand__name"><span class="brand__dot"></span>Terralin</div>
      <div class="brand__tag">Oil Services</div>
    </div>

    <p class="person">Daniel Harker NZCE (Mech) P&amp;P <span class="person__role">, Director</span></p>

    <div class="contact">
      <div class="contact__row">
        <svg class="contact__icon" viewBox="0 0 12 12"><circle cx="6" cy="6" r="5.3" fill="none" stroke="#fff" stroke-width="1.2"/><path d="M4 3.2l1.3 1.4-.7.9c.5 1 1 1.5 1.9 1.9l.9-.7 1.4 1.3-.9 1c-2-.3-4-2.3-4.3-4.4z" fill="#fff"/></svg>
        <span>+61 400 555 018</span>
      </div>
      <div class="contact__row">
        <svg class="contact__icon" viewBox="0 0 12 12"><rect x="1" y="2.5" width="10" height="7" fill="#fff"/><path d="M1 2.5l5 4 5-4" fill="none" stroke="var(--blue)" stroke-width="1"/></svg>
        <span>daniel@terralinoil.co.nz</span>
        <span class="contact__gap"></span>
        <svg class="contact__icon" viewBox="0 0 12 12"><circle cx="6" cy="6" r="5" fill="none" stroke="#fff" stroke-width="1.1"/><ellipse cx="6" cy="6" rx="2.2" ry="5" fill="none" stroke="#fff" stroke-width="1"/><path d="M1 6h10" stroke="#fff" stroke-width="1"/></svg>
        <span>www.terralinoil.com.au</span>
      </div>
      <div class="contact__row"><span>Terralin Oil Services 41 Harbour Road</span></div>
      <div class="contact__row"><span>PO Box 5120 | Kangaroo Point Queensland 4169</span></div>
    </div>
  </section>

  <section class="card card--back">
    <div class="brand">
      <div class="brand__name"><span class="brand__dot"></span>Terralin</div>
      <div class="brand__tag">Oil Services</div>
    </div>
    <p class="back__web">www.terralinoil.com.au</p>
  </section>
</body>
</html>
```